Option Sheet

We need a one page option sheet with a left to right reading of the five options. It should be a one sheet, multiple colors and definitive separations between options This is used in a sales consultation. Backround or colors not in option need to have the follow RGB value (5 red, 20 green, 63 blue)

We added a smaller text file, please change that point

Target Market(s)

Divorce

Industry/Entity Type

Legal

Requirements
Must have
• 1) All five options left to right
• 2)language included in sheet

```html
<!DOCTYPE html>
<html lang="en">
<head>
<meta charset="utf-8">
<title>Divorce – Five Options</title>
<link href="https://fonts.googleapis.com/css2?family=Arimo:ital,wght@0,400;0,700;1,400;1,700&display=swap" rel="stylesheet">
<style>
  :root {
    --backdrop-light: #cfc6a6;
    --backdrop-dark: #a9a691;
    --title-fill: #ffffff;
    --title-shade: #5a5a5a;
    --ink: #000000;
    --frame: #ffffff;
    --opt-blue: #7dd3f6;
    --opt-pink: #f086b4;
    --opt-yellow: #fcf06c;
    --opt-green: #9acd8d;
    --opt-orange: #f9c080;
  }
  * { box-sizing: border-box; margin: 0; padding: 0; }
  html, body { width: 1200px; height: 848px; overflow: hidden; }
  body { font-family: "Arimo", Arial, sans-serif; color: var(--ink); }

  .sheet { position: relative; width: 1200px; height: 848px; overflow: hidden; }

  .backdrop {
    position: absolute; inset: 0;
    background: radial-gradient(circle at 50% 40%, var(--backdrop-light), var(--backdrop-dark));
  }

  .sheet-title {
    position: absolute; top: 28px; left: 0; width: 1200px;
    text-align: center; white-space: nowrap;
    color: var(--title-fill);
    -webkit-text-stroke: 1.5px #6c6c6c;
    text-shadow: 2px 3px 0 var(--title-shade), 5px 7px 8px rgba(0,0,0,.35);
    line-height: 1;
  }
  .sheet-title .main { font-weight: 700; font-size: 92px; letter-spacing: -1px; }
  .sheet-title .sub { font-weight: 400; font-style: italic; font-size: 74px; margin-left: 14px; letter-spacing: 1px; }

  .option {
    position: absolute; top: 150px; height: 660px;
    border: 3px solid var(--frame);
    box-shadow: 3px 4px 8px rgba(0,0,0,.45);
    padding: 6px 8px 0 16px;
  }
  .opt-1 { left: 32px;  width: 192px; background: var(--opt-blue); }
  .opt-2 { left: 238px; width: 211px; background: var(--opt-pink); }
  .opt-3 { left: 461px; width: 194px; background: var(--opt-yellow); }
  .opt-4 { left: 673px; width: 215px; background: var(--opt-green); padding-left: 16px; }
  .opt-5 { left: 903px; width: 261px; background: var(--opt-orange); padding-left: 18px; }

  .option-number {
    font-style: italic; font-weight: 700; font-size: 23px;
    text-align: center; margin-left: -8px; line-height: 1.2;
  }
  .option-name {
    font-weight: 700; font-size: 28px; text-align: center;
    line-height: 1.18; margin: 2px 0 6px -8px; white-space: nowrap;
  }
  .group-label {
    font-style: italic; font-weight: 700; font-size: 17.5px;
    line-height: 22px; margin-top: 2px;
  }
  .points { list-style: none; margin-bottom: 2px; }
  .points li {
    position: relative; padding-left: 19px;
    font-size: 17.5px; line-height: 22.2px;
  }
  .points li::before {
    content: ""; position: absolute; left: 1px; top: 5px;
    width: 10px; height: 10px; border: 2.2px solid var(--ink); border-radius: 50%;
  }
</style>
</head>
<body>
<div class="sheet">
  <div class="backdrop" role="img" aria-label="Interlaced geometric star pattern in beige and grey"></div>

  <h1 class="sheet-title"><span class="main">DIVORCE</span><span class="sub">(Five&nbsp;&nbsp;Options)</span></h1>

  <section class="option opt-1">
    <h2 class="option-number">Option #1:</h2>
    <h3 class="option-name">Do Nothing</h3>
    <p class="group-label">Advantages:</p>
    <ul class="points">
      <li>Stay married</li>
      <li>No life Changes</li>
    </ul>
    <p class="group-label">Disadvantages:</p>
    <ul class="points">
      <li>Remain unhappy, depressed, anxious</li>
      <li>Feel unsafe</li>
      <li>Money and assets may disappear</li>
      <li>Spouse may threaten to leave and/or divorce you</li>
      <li>May cause children to be confused, distressed</li>
      <li>What is going to change?</li>
    </ul>
  </section>

  <section class="option opt-2">
    <h2 class="option-number">Option #2:</h2>
    <h3 class="option-name">Go to<br>Counseling</h3>
    <p class="group-label">Advantages:</p>
    <ul class="points">
      <li>Reconcile marriage</li>
      <li>Help make a better life</li>
    </ul>
    <p class="group-label">Disadvantages:</p>
    <ul class="points">
      <li>Past issues are highlighted and may drudge up old wounds</li>
      <li>It may just clarify the reasons you need to separate and/or divorce</li>
      <li>There is no quick fix for any situation and BOTH parties must be invested and willing to participate</li>
      <li>Bringing a third party into the marriage may cause more confusion and possible distrust</li>
    </ul>
  </section>

  <section class="option opt-3">
    <h2 class="option-number">Option #3:</h2>
    <h3 class="option-name">Do it Yourself</h3>
    <p class="group-label">Advantages:</p>
    <ul class="points">
      <li>No attorney fees</li>
    </ul>
    <p class="group-label">Disadvantages:</p>
    <ul class="points">
      <li>People often find that what is “fair,” may in fact, not be truly fair</li>
      <li>Often times, people do not know the risks</li>
      <li>Complicated legal system</li>
      <li>Unsure how to complete the necessary paperwork and meet the deadlines</li>
      <li>You are too emotional and may be unable to remain clear-headed</li>
      <li>It can be very stressful</li>
    </ul>
  </section>

  <section class="option opt-4">
    <h2 class="option-number">Option #4:</h2>
    <h3 class="option-name">Limited<br>Representation</h3>
    <p class="group-label">Advantages:</p>
    <ul class="points">
      <li>Balance between going alone and our limited involvement in the case</li>
    </ul>
    <p class="group-label">Disadvantages:</p>
    <ul class="points">
      <li>Our terms may not benefit from our legal knowledge</li>
      <li>The legal consequences of your legal documents will not be explained to you so that you can formulate a plan for handling the rest of your case.</li>
      <li>Your spouse or other parties may cause your legal fees to increase significantly without action on your part</li>
    </ul>
  </section>

  <section class="option opt-5">
    <h2 class="option-number">Option #5:</h2>
    <h3 class="option-name">Hire Us</h3>
    <p class="group-label">Advantages:</p>
    <ul class="points">
      <li>Provide peace of mind</li>
      <li>Often saves you money in the long run</li>
      <li>Can stop problems before they start and advise how actions/events may impact your case</li>
      <li>May be able to come to a settlement agreement sooner</li>
      <li>Lessen the emotional stress of one of the worst things that can happen to a person</li>
      <li>Inform you of your rights and what you are entitled to</li>
      <li>Save you time and energy</li>
      <li>Gain the full benefits of our experience</li>
      <li>Provide a shoulder to lean on and a sounding board</li>
    </ul>
    <p class="group-label">Disadvantages:</p>
    <ul class="points">
      <li>Cost</li>
    </ul>
  </section>
</div>
</body>
</html>
```